The Copperline Collective's website for high impact furniture promotions

I am looking for a simple website. we are a promotional company that runs events for furniture stores to increase sales for short periods of time. i would like the website to have about 4 areas to explain our company. I would like it to be simple and user friendly. I would like a link to chatterbook and a contact section. I am attaching our logo that i would like somewhere large or possibly in the backround. I am open to different color schemes. I would like to convey fast paced, modern, reliable. I am open to all different styles and look forward to seeing whats out there. we are looking for a quick turn around, so if we see one that we like quick, we will pick that one thanks
Reason: looking for some really creative designs and want to give a fair amount of time to produce
Target Market(s)
Retail Furniture store owners
Industry/Entity Type
It Company
Number of Pages Required
1 page
Colors
Designer to choose colors to be used in the design.
Look and feel

```html
<!DOCTYPE html>
<html lang="en">
<head>
<meta charset="utf-8">
<title>The Copperline Collective – High Impact Furniture Promotions</title>
<link href="https://fonts.googleapis.com/css2?family=Raleway:wght@700;800;900&family=Lato:wght@400;700;900&display=swap" rel="stylesheet">
<style>
:root{
  --red:#e8443f;
  --red-dark:#c9302c;
  --ink:#1f2430;
  --navy:#262c38;
  --grey-bg:#eef0f3;
  --text:#555b66;
  --white:#ffffff;
}
*{margin:0;padding:0;box-sizing:border-box}
html,body{width:1200px;height:5322px;overflow:hidden}
body{position:relative;font-family:'Lato',sans-serif;color:var(--text);background:var(--white)}
.abs{position:absolute}
.section{position:absolute;left:0;width:1200px;overflow:hidden}
.heading{font-family:'Raleway',sans-serif;font-weight:900;color:var(--ink)}
.underline{position:absolute;height:6px;width:56px;background:var(--red)}

/* hero */
.hero{top:0;height:561px;background:linear-gradient(180deg,#2b2a2a 0%,#4a4540 45%,#2f2b28 100%)}
.hero-photo{position:absolute;inset:0;background:radial-gradient(ellipse at 60% 70%,#6b6158 0%,#3e3833 55%,#1f1d1c 100%);opacity:.95}
.brand{position:absolute;left:130px;top:30px;width:150px;text-align:center}
.brand-dot{width:104px;height:104px;border-radius:50%;background:var(--red);margin:0 auto 14px}
.brand-name{font-family:'Lato',sans-serif;font-weight:700;color:var(--white);font-size:19px;line-height:1.25;letter-spacing:1px}
.nav{position:absolute;top:50px;left:392px;display:flex;gap:0;align-items:center}
.nav a{color:var(--white);text-decoration:none;font-family:'Lato',sans-serif;font-weight:900;font-size:14px;letter-spacing:.5px;padding:9px 14px}
.nav a.active{background:var(--red);border-radius:3px;margin-left:10px}
.social{position:absolute;left:136px;top:238px;display:flex;gap:22px;align-items:center}
.social span{display:block;width:20px;height:20px;border-radius:50%;background:var(--white)}
.hero-title{position:absolute;left:0;width:1200px;top:258px;text-align:center;font-family:'Raleway',sans-serif;font-weight:900;color:var(--white)}
.hero-title .l1{display:block;font-size:56px;line-height:64px;color:#f3f0c8}
.hero-title .l2{display:block;font-size:82px;line-height:84px}

/* promo band */
.promo{top:561px;height:504px;background:var(--red)}
.promo h2{position:absolute;top:180px;width:1200px;text-align:center;color:var(--white);font-family:'Raleway',sans-serif;font-weight:900}
.promo h2 .sm{display:block;font-size:44px;line-height:54px;font-weight:800}
.promo h2 .lg{display:block;font-size:72px;line-height:78px;letter-spacing:2px}

/* steps */
.steps{top:1065px;height:437px;background:var(--white)}
.steps h2{position:absolute;top:0;width:1200px;text-align:center}
.steps h2 .sm{display:block;font-family:'Raleway',sans-serif;font-weight:800;font-size:42px;color:var(--ink);line-height:50px}
.steps h2 .lg{display:block;font-family:'Raleway',sans-serif;font-weight:900;font-size:58px;color:var(--red);line-height:64px}
.step{position:absolute;top:180px;width:210px}
.step-icon{width:92px;height:92px;border-radius:50%;background:var(--white);box-shadow:0 6px 18px rgba(0,0,0,.12);border:3px solid #f4f4f4;position:relative;margin-left:40px}
.step-icon svg{position:absolute;left:22px;top:22px}
.step-num{position:absolute;right:-12px;top:-10px;width:34px;height:34px;border-radius:50%;background:var(--red);color:var(--white);font-family:'Lato';font-weight:900;font-size:17px;text-align:center;line-height:34px}
.step h3{margin-top:40px;font-family:'Lato';font-weight:900;font-size:16px;color:var(--ink);letter-spacing:.3px}
.step p{font-size:15px;line-height:21px;margin-top:4px}
.step-arrow{position:absolute;top:188px}

/* photo band */
.crowd{top:1502px;height:592px;background:linear-gradient(180deg,#5a5b5e 0%,#7d7a78 40%,#9a8f86 70%,#6c655e 100%)}

/* about */
.about{top:2094px;height:586px;background:var(--white)}
.about .heading{position:absolute;left:150px;top:140px;font-size:58px}
.about .underline{left:150px;top:215px}
.about p{position:absolute;left:150px;width:420px;font-size:15.5px;line-height:25px}
.about-frame{position:absolute;left:950px;top:125px;width:300px;height:480px;border:7px solid var(--red)}
.about-video{position:absolute;left:632px;top:190px;width:440px;height:340px;background:linear-gradient(135deg,#eef0ec 0%,#c9cfc6 50%,#8e9488 100%)}
.play{position:absolute;left:190px;top:140px;width:60px;height:60px;border-radius:50%;background:var(--white);box-shadow:0 4px 14px rgba(0,0,0,.2)}

/* team */
.team{top:2680px;height:550px;background:var(--grey-bg)}
.team .heading{position:absolute;left:150px;top:70px;font-size:58px}
.team .underline{left:150px;top:145px}
.pager{position:absolute;top:85px;display:flex;gap:6px;left:957px}
.pager span{display:block;width:40px;height:40px;background:var(--white);position:relative}
.pager span.on{background:var(--red)}
.member{position:absolute;top:188px;width:190px}
.member .pic{width:180px;height:185px}
.member .pic.feature{outline:6px solid var(--red)}
.member h4{margin-top:20px;font-family:'Raleway',sans-serif;font-weight:900;font-size:23px;color:var(--ink)}
.member h4 em{font-style:normal;color:var(--red)}
.member p{font-size:15px;margin-top:2px}

/* news */
.news{top:3230px;height:817px;background:var(--white)}
.news .heading{position:absolute;left:150px;top:70px;font-size:58px}
.news .underline{left:150px;top:145px}
.post{position:absolute;top:196px;width:270px}
.post .pic{width:270px;height:195px}
.post .pic.feature{outline:7px solid var(--red)}
.post h4{margin-top:22px;font-family:'Lato';font-weight:900;font-size:15px;line-height:20px;color:var(--ink)}
.post p{margin-top:10px;font-size:14px;line-height:21px}
.btn{position:absolute;background:var(--red);color:var(--white);font-family:'Lato';font-weight:900;font-size:15px;letter-spacing:.5px;display:flex;align-items:center;gap:8px;justify-content:center}

/* testimonials */
.testi{top:4047px;height:568px;background:var(--red)}
.testi .heading{position:absolute;top:105px;width:1200px;text-align:center;color:var(--white);font-size:58px}
.testi .underline{left:572px;top:180px;background:var(--white)}
.quote{position:absolute;left:170px;top:242px;width:860px;text-align:center;color:var(--white);font-style:italic;font-size:19px;line-height:37px}
.quote b{font-family:'Raleway';font-weight:900;font-style:normal;font-size:40px;vertical-align:-8px}
.avatar{position:absolute;left:570px;top:438px;width:60px;height:60px;border-radius:50%;background:#f2a19a}
.client{position:absolute;top:508px;width:1200px;text-align:center;color:var(--white)}
.client strong{display:block;font-family:'Lato';font-weight:900;font-size:17px}
.client span{font-style:italic;font-size:14px}
.side-arrow{position:absolute;top:300px}

/* map + footer */
.map{top:4615px;height:213px;background:linear-gradient(90deg,#e7e6e1 0%,#efeee9 50%,#e4e3dd 100%)}
.footer{top:4828px;height:494px;background:var(--navy)}
.foot-brand{position:absolute;left:130px;top:170px;width:260px;text-align:center}
.foot-brand .brand-dot{width:120px;height:120px}
.foot-brand .brand-name{font-size:22px}
.contact-card{position:absolute;left:433px;top:4775px;width:342px;height:547px;background:var(--white)}
.contact-card h3{text-align:center;margin-top:28px;font-family:'Raleway';font-weight:900;font-size:38px;color:var(--ink)}
.contact-card .underline{left:143px;top:85px}
.field{margin:0 auto;width:250px;border-bottom:1px solid #cfd2d8;text-align:center;font-size:15px;color:#6a707b;padding:14px 0 10px}
.fields{margin-top:42px}
.address{position:absolute;left:810px;top:5015px;width:360px;color:#c9ccd3}
.address h4{font-family:'Lato';font-weight:900;font-size:19px;letter-spacing:1px;color:var(--red)}
.addr-row{display:flex;gap:14px;margin-top:18px;align-items:flex-start}
.addr-row .txt{font-size:14px;line-height:21px}
.addr-row .txt strong{color:var(--white);display:block}
.phone{font-size:26px;color:#dfe2e8}
.foot-social{position:absolute;left:812px;top:5245px;display:flex;gap:26px}
.foot-social span{display:block;width:22px;height:22px;border-radius:50%;background:var(--red)}
</style>
</head>
<body>

<!-- HERO -->
<section class="section hero">
  <div class="hero-photo" role="img" aria-label="Furniture showroom interior with rows of sofas and recliners"></div>
  <div class="brand">
    <div class="brand-dot"></div>
    <div class="brand-name">The Copperline Collective</div>
  </div>
  <nav class="nav">
    <a href="#">HOME</a><a href="#">ABOUT</a><a href="#">TRADE SHOW</a><a href="#">SERVICES</a><a href="#">TEAM</a><a href="#">GALLERY</a><a href="#">VIDEO</a><a href="#">NEWS</a><a href="#" class="active">CONTACT US</a>
  </nav>
  <div class="social" aria-label="Social links: chatterbook, chirpline, circleplus, linkpro">
    <span></span><span></span><span></span><span></span>
  </div>
  <h1 class="hero-title"><span class="l1">Let us plan your</span><span class="l2">next BIG event</span></h1>
</section>

<!-- PROMOTIONS BAND -->
<section class="section promo">
  <h2><span class="sm">High Impact Furniture</span><span class="lg">PROMOTIONS</span></h2>
</section>

<!-- STEPS -->
<section class="section steps">
  <h2><span class="sm">Increase sales in</span><span class="lg">4 Easy Steps</span></h2>

  <div class="step" style="left:148px">
    <div class="step-icon"><svg width="48" height="48" viewBox="0 0 48 48" fill="none" stroke="#e8443f" stroke-width="2.5"><rect x="6" y="10" width="36" height="32" rx="3"/><line x1="6" y1="19" x2="42" y2="19"/><line x1="15" y1="5" x2="15" y2="14"/><line x1="33" y1="5" x2="33" y2="14"/><rect x="13" y="25" width="5" height="5"/><rect x="22" y="25" width="5" height="5"/><rect x="31" y="25" width="5" height="5"/><rect x="13" y="33" width="5" height="5"/><rect x="22" y="33" width="5" height="5"/></svg><div class="step-num">1</div></div>
    <h3>LOREM IPSUM DOLOR</h3>
    <p>Mauris accumsan, purus sed maximus, lorem nulla volutpat diam.</p>
  </div>
  <div class="step" style="left:383px">
    <div class="step-icon"><svg width="48" height="48" viewBox="0 0 48 48" fill="none" stroke="#e8443f" stroke-width="2.5"><path d="M10 26v-8a4 4 0 0 1 4-4h20a4 4 0 0 1 4 4v8"/><rect x="4" y="24" width="8" height="12" rx="2"/><rect x="36" y="24" width="8" height="12" rx="2"/><rect x="12" y="27" width="24" height="9"/><line x1="8" y1="36" x2="8" y2="41"/><line x1="40" y1="36" x2="40" y2="41"/></svg><div class="step-num">2</div></div>
    <h3>LOREM IPSUM DOLOR</h3>
    <p>Mauris accumsan, purus sed maximus, lorem nulla volutpat diam.</p>
  </div>
  <div class="step" style="left:618px">
    <div class="step-icon"><svg width="48" height="48" viewBox="0 0 48 48" fill="none" stroke="#e8443f" stroke-width="2.5"><line x1="6" y1="42" x2="42" y2="42"/><rect x="10" y="30" width="5" height="12"/><rect x="19" y="24" width="5" height="18"/><rect x="28" y="18" width="5" height="24"/><rect x="37" y="10" width="5" height="32"/><polyline points="8,24 18,14 26,18 38,6"/></svg><div class="step-num">3</div></div>
    <h3>LOREM IPSUM DOLOR</h3>
    <p>Mauris accumsan, purus sed maximus, lorem nulla volutpat diam.</p>
  </div>
  <div class="step" style="left:853px">
    <div class="step-icon"><svg width="48" height="48" viewBox="0 0 48 48" fill="none" stroke="#e8443f" stroke-width="2.5"><path d="M40 8c-10 0-18 6-22 16l6 6c10-4 16-12 16-22z"/><circle cx="30" cy="18" r="3"/><path d="M18 24l-8 2 4-8 8-2"/><path d="M24 30l-2 8 8-4 2-8"/><path d="M14 34l-6 6"/></svg><div class="step-num">4</div></div>
    <h3>LOREM IPSUM DOLOR</h3>
    <p>Mauris accumsan, purus sed maximus, lorem nulla volutpat diam.</p>
  </div>

  <svg class="step-arrow" style="left:296px" width="64" height="34" viewBox="0 0 64 34" fill="none" stroke="#1f2430" stroke-width="2"><path d="M4 28C18 6 44 4 58 20"/><polyline points="50,20 58,20 58,12"/></svg>
  <svg class="step-arrow" style="left:531px" width="64" height="34" viewBox="0 0 64 34" fill="none" stroke="#1f2430" stroke-width="2"><path d="M4 6C18 28 44 30 58 14"/><polyline points="50,14 58,14 58,22"/></svg>
  <svg class="step-arrow" style="left:766px" width="64" height="34" viewBox="0 0 64 34" fill="none" stroke="#1f2430" stroke-width="2"><path d="M4 28C18 6 44 4 58 20"/><polyline points="50,20 58,20 58,12"/></svg>
</section>

<!-- CROWD PHOTO -->
<section class="section crowd" role="img" aria-label="Long queue of shoppers lined up outside a furniture store during a promotion event"></section>

<!-- ABOUT -->
<section class="section about">
  <h2 class="heading">ABOUT US</h2>
  <div class="underline"></div>
  <p style="top:262px">Lorem ipsum dolor sit amet, consectetur adipiscing elit. Mauris accumsan, purus vel hendrerit maximus, lorem nulla venenatis elit, vitae volutpat diam ipsum id ligula.</p>
  <p style="top:380px">Duis dolor urna, accumsan a augue et, feugiat sagittis elit. Mauris scelerisque orci vitae dui fermentum, non mollis lectus volutpat. Nullam tincidunt enim lobortis ultricies gravida. Curabitur scelerisque ac tortor eget aliquet. In et ultricies ligula, non lacinia lorem.</p>
  <div class="about-frame"></div>
  <div class="about-video" role="img" aria-label="Video still of a bright living room with a grey sofa and armchair">
    <div class="play"><svg width="60" height="60" viewBox="0 0 60 60"><polygon points="25,19 25,41 42,30" fill="#e8443f"/></svg></div>
  </div>
</section>

<!-- TEAM -->
<section class="section team">
  <h2 class="heading">OUR TEAM</h2>
  <div class="underline"></div>
  <div class="pager">
    <span><svg width="40" height="40" viewBox="0 0 40 40"><polyline points="23,14 17,20 23,26" fill="none" stroke="#c3c6cc" stroke-width="2.5"/></svg></span>
    <span class="on"><svg width="40" height="40" viewBox="0 0 40 40"><polyline points="17,14 23,20 17,26" fill="none" stroke="#fff" stroke-width="2.5"/></svg></span>
  </div>
  <div class="member" style="left:160px">
    <div class="pic" role="img" aria-label="Portrait of the founder" style="background:linear-gradient(160deg,#9aa1a8,#4d5259)"></div>
    <h4><em>Owen</em> Marsh</h4><p>Founder &amp; CEO</p>
  </div>
  <div class="member" style="left:390px">
    <div class="pic feature" role="img" aria-label="Portrait of the co-founder" style="background:linear-gradient(160deg,#d9b98f,#8a6a4a)"></div>
    <h4><em>Nina</em> Hollis</h4><p>Co-Founder</p>
  </div>
  <div class="member" style="left:628px">
    <div class="pic" role="img" aria-label="Portrait of the managing director" style="background:linear-gradient(160deg,#c8c4bd,#5e5a55)"></div>
    <h4><em>Derek</em> Vance</h4><p>Managing Director</p>
  </div>
  <div class="member" style="left:859px">
    <div class="pic" role="img" aria-label="Portrait of the advert manager" style="background:linear-gradient(160deg,#b7b2ab,#55524e)"></div>
    <h4><em>Felix</em> Harlow</h4><p>Advert Manager</p>
  </div>
</section>

<!-- NEWS -->
<section class="section news">
  <h2 class="heading">LATEST NEWS</h2>
  <div class="underline"></div>
  <article class="post" style="left:160px">
    <div class="pic" role="img" aria-label="Modern living room with bookshelves and sofa" style="background:linear-gradient(135deg,#cfc9c0,#6f6a63)"></div>
    <h4>1 YEAR AGO, WE WERE JUST WRAPPING UP SEASON. NOW WE RULE FRIDAY NIGHTS.</h4>
    <p>Lorem ipsum dolor sit amet, cons adipiscing elit. Mauris accumsan, pure vel hendrerit maximus.</p>
  </article>
  <article class="post" style="left:465px">
    <div class="pic feature" role="img" aria-label="Dining table with chairs in a warm interior" style="background:linear-gradient(135deg,#a07a56,#4b3a2b)"></div>
    <h4>1 YEAR AGO, WE WERE JUST WRAPPING UP SEASON. NOW WE RULE FRIDAY NIGHTS.</h4>
    <p>Lorem ipsum dolor sit amet, cons adipiscing elit. Mauris accumsan, pure vel hendrerit maximus.</p>
  </article>
  <article class="post" style="left:772px">
    <div class="pic" role="img" aria-label="Bright room with wooden sideboard and lamps" style="background:linear-gradient(135deg,#efe9df,#b9a58a)"></div>
    <h4>1 YEAR AGO, WE WERE JUST WRAPPING UP SEASON. NOW WE RULE FRIDAY NIGHTS.</h4>
    <p>Lorem ipsum dolor sit amet, cons adipiscing elit. Mauris accumsan, pure vel hendrerit maximus.</p>
  </article>
  <a class="btn" href="#" style="left:462px;top:660px;width:236px;height:50px;text-decoration:none">READ ALL NEWS
    <svg width="20" height="16" viewBox="0 0 20 16" fill="#fff"><polygon points="0,8 20,0 14,16 10,10"/></svg></a>
</section>

<!-- TESTIMONIALS -->
<section class="section testi">
  <h2 class="heading">TESTIMONIALS</h2>
  <div class="underline"></div>
  <svg class="side-arrow" style="left:118px" width="20" height="36" viewBox="0 0 20 36"><polyline points="16,4 4,18 16,32" fill="none" stroke="#f59b95" stroke-width="3"/></svg>
  <svg class="side-arrow" style="left:1078px" width="20" height="36" viewBox="0 0 20 36"><polyline points="4,4 16,18 4,32" fill="none" stroke="#f59b95" stroke-width="3"/></svg>
  <p class="quote"><b>“</b> Fusce ut mattis lacus, vel accumsan ligula. Sed cursus diam vel odio pellentes que cursus. Donec augue diam, malesuada ut fringilla convallis, mattis ut neque. Ut eget suscipit enim. Curabitur ullam metus, a tincidunt erat aliquam nec. Suspendisse risus ex, gravida et leo vel, posuere ornare ex. <b>”</b></p>
  <div class="avatar" role="img" aria-label="Client portrait"></div>
  <div class="client"><strong>PAUL DENTON</strong><span>Client</span></div>
</section>

<!-- MAP -->
<section class="section map" role="img" aria-label="Street map showing the office location">
  <svg class="abs" style="left:730px;top:85px" width="26" height="36" viewBox="0 0 26 36"><path d="M13 0C6 0 0 6 0 13c0 10 13 23 13 23s13-13 13-23C26 6 20 0 13 0z" fill="#e8443f"/><circle cx="13" cy="13" r="5" fill="#fff"/></svg>
</section>

<!-- FOOTER -->
<section class="section footer">
  <div class="foot-brand">
    <div class="brand-dot"></div>
    <div class="brand-name">The Copperline Collective</div>
  </div>
</section>

<div class="contact-card">
  <h3>CONTACT US</h3>
  <div class="underline"></div>
  <div class="fields">
    <div class="field">Enter Your Name</div>
    <div class="field">Enter Your Email</div>
    <div class="field">Enter Your Phone No.</div>
    <div class="field">Subject</div>
    <div class="field" style="height:94px">Enter Your Message</div>
  </div>
  <a class="btn" href="#" style="left:92px;top:460px;width:158px;height:46px;text-decoration:none">SUBMIT
    <svg width="20" height="16" viewBox="0 0 20 16" fill="#fff"><polygon points="0,8 20,0 14,16 10,10"/></svg></a>
</div>

<div class="address">
  <h4>OUR ADDRESS</h4>
  <div class="addr-row">
    <svg width="18" height="24" viewBox="0 0 18 24"><path d="M9 0C4 0 0 4 0 9c0 7 9 15 9 15s9-8 9-15C18 4 14 0 9 0z" fill="none" stroke="#e8443f" stroke-width="2"/><circle cx="9" cy="9" r="3" fill="#e8443f"/></svg>
    <div class="txt"><strong>The Copperline Collective</strong>418 Alder Ridge Rd, Brookfield,<br>North Carolina 27000, United States</div>
  </div>
  <div class="addr-row" style="align-items:center">
    <svg width="20" height="20" viewBox="0 0 24 24"><path d="M5 2h4l2 5-3 2c1 3 4 6 7 7l2-3 5 2v4c0 1-1 3-3 3C10 22 2 14 2 5c0-2 2-3 3-3z" fill="none" stroke="#e8443f" stroke-width="2"/></svg>
    <div class="phone">555 014 2273</div>
  </div>
  <div class="addr-row" style="align-items:center">
    <svg width="20" height="16" viewBox="0 0 20 16"><rect x="1" y="1" width="18" height="14" fill="none" stroke="#e8443f" stroke-width="2"/><polyline points="1,1 10,9 19,1" fill="none" stroke="#e8443f" stroke-width="2"/></svg>
    <div class="txt">hello@copperlinepromotions.example</div>
  </div>
</div>
<div class="foot-social" aria-label="Social links: chatterbook, chirpline, circleplus, linkpro">
  <span></span><span></span><span></span><span></span>
</div>

</body>
</html>
```